Business Card Design for Flood Rescue 360 - Property Restoration Professionals

I need a business card designed for Flood Rescue 360. We are a full-service property restoration solution. Providing water, fire, smoke & storm restoration as well as mold remediation and full remodel or reconstruction to homes and businesses across Dallas-Fort Worth, TX.
Target Market(s)
home and business owners with insurance covered property damage from water, fire or storm related damage
Industry/Entity Type
property restoration
Contact Information for Business Card
Marcus Pelley General Manager Cell: 214-555-0193 Office: 469-555-0148 email: Marcus@FloodRescue360.example services: Water, Fire, Mold, Reconstruction Tagline: Fast Help When Every Minute Counts!
Look and feel
Each slider illustrates characteristics of the customer's brand and the style your logo design should communicate.

```html
<!DOCTYPE html>
<html lang="en">
<head>
<meta charset="utf-8">
<title>Flood Rescue 360 – Business Card</title>
<link href="https://fonts.googleapis.com/css2?family=Montserrat:wght@400;500;800&display=swap" rel="stylesheet">
<style>
  :root {
    --backdrop: #4a4a4a;
    --card: #161616;
    --accent: #0bb0e6;
    --ink: #f2f2f2;
    --muted: #9a9a9a;
    --emblem: #2a2a2a;
  }
  * { box-sizing: border-box; margin: 0; padding: 0; }
  html, body { width: 1200px; height: 801px; overflow: hidden; }
  body {
    background: var(--backdrop);
    font-family: "Montserrat", sans-serif;
    color: var(--ink);
    position: relative;
  }
  .card {
    position: absolute;
    top: 246px;
    width: 540px;
    height: 309px;
    background: var(--card);
    border-bottom: 3px solid var(--accent);
    box-shadow: 0 18px 40px rgba(0,0,0,.45);
    overflow: hidden;
  }
  .card--front { left: 40px; }
  .card--back { left: 620px; border-left: 3px solid var(--accent); }

  /* front */
  .brand {
    position: absolute;
    left: 34px; top: 96px;
    width: 210px;
    display: flex; align-items: center; gap: 10px;
  }
  .brand__mark {
    width: 22px; height: 22px; flex: none;
    border-radius: 50%;
    background: var(--accent);
  }
  .brand__name {
    font-weight: 800;
    font-size: 26px;
    line-height: 1.05;
    text-transform: uppercase;
    color: var(--accent);
    letter-spacing: .5px;
  }
  .divider {
    position: absolute;
    left: 262px; top: 40px;
    width: 2px; height: 170px;
    background: var(--accent);
  }
  .contact {
    position: absolute;
    left: 282px; top: 38px;
    right: 20px;
  }
  .contact__name {
    font-weight: 800;
    font-size: 24px;
    color: var(--accent);
    line-height: 1.1;
  }
  .contact__role {
    font-size: 13px;
    font-weight: 400;
    margin: 4px 0 16px;
  }
  .contact__list { list-style: none; }
  .contact__item {
    display: flex; align-items: center; gap: 8px;
    font-size: 12.5px;
    line-height: 1.9;
    white-space: nowrap;
  }
  .contact__icon { width: 12px; height: 12px; flex: none; }
  .tagline {
    position: absolute;
    left: 0; right: 0; bottom: 26px;
    text-align: center;
    font-size: 15px;
    font-weight: 400;
  }

  /* back */
  .emblem {
    position: absolute;
    left: 0; right: 0; top: 62px;
    display: flex; flex-direction: column; align-items: center; gap: 12px;
  }
  .emblem__mark {
    width: 96px; height: 96px;
    border-radius: 50%;
    background: var(--emblem);
  }
  .emblem__name {
    font-weight: 800;
    font-size: 20px;
    text-transform: uppercase;
    color: var(--muted);
    letter-spacing: 1px;
  }
  .services {
    position: absolute;
    left: 0; right: 0; bottom: 34px;
    text-align: center;
  }
  .services__title {
    font-weight: 800;
    font-size: 22px;
    color: var(--accent);
    letter-spacing: 1px;
  }
  .services__list {
    margin-top: 4px;
    font-size: 16px;
    display: flex; justify-content: center; align-items: center; gap: 8px;
  }
  .services__dot {
    width: 8px; height: 8px; border-radius: 50%;
    background: var(--accent);
  }
</style>
</head>
<body>
  <section class="card card--front" aria-label="Business card front">
    <div class="brand">
      <span class="brand__mark"></span>
      <span class="brand__name">Flood Rescue 360</span>
    </div>
    <div class="divider"></div>
    <div class="contact">
      <h1 class="contact__name">Marcus Pelley</h1>
      <p class="contact__role">General Manager</p>
      <ul class="contact__list">
        <li class="contact__item">
          <svg class="contact__icon" viewBox="0 0 12 12"><rect x="3" y="0.5" width="6" height="11" rx="1" fill="none" stroke="#0bb0e6" stroke-width="1.2"/><circle cx="6" cy="9.5" r=".7" fill="#0bb0e6"/></svg>
          214-555-0193
        </li>
        <li class="contact__item">
          <svg class="contact__icon" viewBox="0 0 12 12"><path d="M1 4c0-2 10-2 10 0v1.5H8.5V4h-5v1.5H1z" fill="#0bb0e6"/><rect x="2.5" y="6" width="7" height="5" rx="1" fill="#0bb0e6"/></svg>
          469-555-0148
        </li>
        <li class="contact__item">
          <svg class="contact__icon" viewBox="0 0 12 12"><rect x=".5" y="2" width="11" height="8" fill="none" stroke="#0bb0e6" stroke-width="1.2"/><path d="M.5 2l5.5 4.5L11.5 2" fill="none" stroke="#0bb0e6" stroke-width="1.2"/></svg>
          Marcus@FloodRescue360.example
        </li>
        <li class="contact__item">
          <svg class="contact__icon" viewBox="0 0 12 12"><circle cx="6" cy="6" r="5.3" fill="none" stroke="#0bb0e6" stroke-width="1.2"/><path d="M.7 6h10.6M6 .7c-3 3-3 7.6 0 10.6M6 .7c3 3 3 7.6 0 10.6" fill="none" stroke="#0bb0e6" stroke-width="1"/></svg>
          FloodRescue360.example
        </li>
      </ul>
    </div>
    <p class="tagline">Fast Help When Every Minute Counts!</p>
  </section>

  <section class="card card--back" aria-label="Business card back">
    <div class="emblem">
      <span class="emblem__mark"></span>
      <span class="emblem__name">Flood Rescue 360</span>
    </div>
    <div class="services">
      <h2 class="services__title">SERVICES</h2>
      <p class="services__list">
        <span>Water</span><span class="services__dot"></span>
        <span>Fire</span><span class="services__dot"></span>
        <span>Mold</span><span class="services__dot"></span>
        <span>Reconstruction</span>
      </p>
    </div>
  </section>
</body>
</html>
```